MRT Property - Business Cards

Looking for a business card & general letterhead, signage etc design for our new logo.

Colours:
000a20
0056a2
00b5ef
0088ce
68cef2

Fonts:
Poppins
Karla

Please keep look and feel of new brand - example in the zip package I sent.

```html
<!DOCTYPE html>
<html lang="en">
<head>
<meta charset="utf-8">
<title>MRT Property – Business Cards</title>
<link rel="stylesheet" href="https://fonts.googleapis.com/css2?family=Montserrat:wght@400;500;700&family=Delius&display=swap">
<style>
  :root {
    --backdrop: #7d6a52;
    --card-white: #ffffff;
    --brand-navy: #000a20;
    --brand-blue: #0056a2;
    --brand-mid: #0088ce;
    --brand-sky: #00b5ef;
    --back-blue: #0b55a4;
    --back-mark: #0a4a92;
    --text-dark: #111111;
  }
  * { margin: 0; padding: 0; box-sizing: border-box; }
  html, body { width: 900px; height: 1200px; overflow: hidden; }
  body { background: var(--backdrop); position: relative; font-family: "Montserrat", sans-serif; }

  .card { position: absolute; border-radius: 24px; overflow: hidden; }
  .card-front { left: 80px; top: 131px; width: 742px; height: 440px; background: var(--card-white); }
  .card-back { left: 78px; top: 638px; width: 744px; height: 440px; background: var(--back-blue); }

  .brand-name {
    position: absolute; left: 72px; top: 214px; width: 270px;
    font-family: "Montserrat", sans-serif; font-weight: 700; font-size: 31px;
    color: var(--brand-blue); text-align: center; letter-spacing: 0.5px;
  }
  .divider { position: absolute; left: 348px; top: 121px; width: 2px; height: 224px; background: var(--brand-blue); }

  .contact-block { position: absolute; left: 365px; top: 120px; color: var(--text-dark); }
  .person-name { font-family: "Delius", cursive; font-size: 30px; color: var(--brand-blue); line-height: 36px; }
  .person-role { font-size: 15px; line-height: 20px; }
  .address { margin-top: 23px; font-size: 15px; line-height: 21px; }
  .contact-list { list-style: none; margin-top: 22px; }
  .contact-list li { display: flex; align-items: center; font-size: 15px; height: 28px; }
  .contact-list svg { width: 16px; height: 16px; margin-right: 11px; fill: var(--brand-blue); flex: none; }

  .back-name {
    position: absolute; left: 0; right: 0; top: 176px; text-align: center;
    font-family: "Montserrat", sans-serif; font-weight: 700; font-size: 78px;
    color: var(--back-mark); letter-spacing: 1px;
  }
</style>
</head>
<body>
  <section class="card card-front">
    <div class="brand-name">MRT Property</div>
    <div class="divider"></div>
    <div class="contact-block">
      <div class="person-name">Daniel Hart</div>
      <div class="person-role">Mnaging Director</div>
      <div class="address">218 Maple Ridge Ave Suite<br>40 Dayton Ohio 45402</div>
      <ul class="contact-list">
        <li>
          <svg viewBox="0 0 24 24" aria-hidden="true"><path d="M6.6 10.8a15.1 15.1 0 0 0 6.6 6.6l2.2-2.2a1 1 0 0 1 1-.25 11.4 11.4 0 0 0 3.6.57 1 1 0 0 1 1 1V20a1 1 0 0 1-1 1A17 17 0 0 1 3 4a1 1 0 0 1 1-1h3.5a1 1 0 0 1 1 1c0 1.25.2 2.45.57 3.57a1 1 0 0 1-.25 1z"/></svg>
          1 (555) 204-7391
        </li>
        <li>
          <svg viewBox="0 0 24 24" aria-hidden="true"><path d="M2 5h20v14H2z M2 5l10 7 10-7" /><path d="M3 6.2l9 6.3 9-6.3V18H3z" fill="#fff"/></svg>
          info@mrtproperty.com
        </li>
        <li>
          <svg viewBox="0 0 24 24" aria-hidden="true"><circle cx="12" cy="12" r="10"/><path d="M2 12h20M12 2c3 3 3 17 0 20M12 2c-3 3-3 17 0 20" stroke="#fff" stroke-width="1.4" fill="none"/></svg>
          www.mrtproperty.com
        </li>
      </ul>
    </div>
  </section>

  <section class="card card-back">
    <div class="back-name">MRT Property</div>
  </section>
</body>
</html>
```